High-end construction company needs a business card design

We need a modern looking business card that draws people in, is memorable and looks so good people will want to sick it on their fridges.
On the first side what is needed are:
Logo
My name - Tomasz Brelwik
Title - Managing Director
Website - www.varkelt.co.uk
Email - tomasz@varkelt.co.uk
Telephone - 020 5194 6281
Mobile - 07845139072
On the back side was is needed is a list of all the services we provide:
-Kitchen Renovations
-Bathroom Renovations
-House Renovations
-Garage Conversions
-Extensions
-Loft Conversions
-Conservatories
-Carpentry
-Tiling
-Electrical
-Plumbing & Heating
-Bricklaying
-Landscaping
-Decorating
-Plastering
We would like the colours to be the same shades as on the logo with grey or black for the words.
Target Market(s)
Anyone who needs building work done
Contact Information for Business Card
This business card is for a construction company which strives to deliver excellent service and quality.
The look and feel of the card should represent this.
Requirements
Must have
- On the first side what is needed are:
Logo
My name - Tomasz Brelwik
Title - Managing Director
Website - www.varkelt.co.uk
Email - tomasz@varkelt.co.uk
Telephone - 020 5194 6281
Mobile - 07845139072
Nice to have
- Cool looking features

```html
<!DOCTYPE html>
<html lang="en">
<head>
<meta charset="utf-8">
<title>Varkelt Construction Ltd – Business Card</title>
<link rel="stylesheet" href="https://fonts.googleapis.com/css2?family=Play:wght@400;700&display=swap">
<style>
  :root {
    --page-bg: #8a8a8a;
    --panel-green: #4a8c3f;
    --brand-green: #6fbe44;
    --card-white: #ffffff;
    --card-dark: #2b2b2b;
    --text-light: #ffffff;
  }
  * { margin: 0; padding: 0; box-sizing: border-box; }
  html, body {
    width: 1125px; height: 1200px; overflow: hidden;
    background: var(--page-bg);
    font-family: "Play", Arial, sans-serif;
  }
  .card {
    position: absolute;
    left: 171px;
    width: 826px;
    height: 471px;
    overflow: hidden;
  }
  .card--front { top: 106px; background: var(--card-white); }
  .card--back { top: 639px; background: var(--card-dark); }

  .front-panel { position: absolute; inset: 0; }

  .contact-block {
    position: absolute;
    left: 63px;
    top: 62px;
    color: var(--text-light);
  }
  .contact-name {
    color: var(--brand-green);
    font-weight: 700;
    font-size: 33px;
    letter-spacing: 0.5px;
    line-height: 1.1;
    text-transform: uppercase;
  }
  .contact-title {
    font-weight: 700;
    font-size: 21px;
    line-height: 1.2;
    margin-bottom: 22px;
  }
  .contact-list { list-style: none; }
  .contact-list li {
    display: flex;
    align-items: center;
    font-weight: 700;
    font-size: 21.5px;
    line-height: 26.5px;
  }
  .contact-list svg { width: 16px; height: 16px; margin-right: 14px; flex: none; }

  .brand-name {
    position: absolute;
    color: var(--brand-green);
    font-weight: 700;
    text-align: center;
    line-height: 1;
    text-transform: uppercase;
  }
  .brand-name .brand-word { display: block; }
  .brand-name .brand-suffix { display: block; letter-spacing: 3px; }

  .card--front .brand-name { right: 48px; top: 330px; }
  .card--front .brand-word { font-size: 84px; letter-spacing: 1px; }
  .card--front .brand-suffix { font-size: 22px; margin-top: 8px; }

  .card--back .brand-name { left: 0; right: 0; top: 180px; }
  .card--back .brand-word { font-size: 78px; letter-spacing: 1px; }
  .card--back .brand-suffix { font-size: 20px; margin-top: 8px; }

  .service-list {
    position: absolute;
    left: 0; right: 0; top: 310px;
    text-align: center;
    color: var(--text-light);
    font-size: 17.5px;
    line-height: 23.5px;
  }
  .tick {
    display: inline-block;
    width: 15px; height: 13px;
    margin: 0 3px;
    vertical-align: -1px;
  }
</style>
</head>
<body>

<section class="card card--front" aria-label="Business card front">
  <svg class="front-panel" viewBox="0 0 826 471" preserveAspectRatio="none" aria-hidden="true">
    <polygon points="0,0 572,0 231,471 0,471" fill="var(--panel-green)"/>
  </svg>

  <div class="contact-block">
    <h1 class="contact-name">Tomasz Brelwik</h1>
    <p class="contact-title">Managing Director</p>
    <ul class="contact-list">
      <li>
        <svg viewBox="0 0 16 16" aria-hidden="true"><path fill="var(--brand-green)" d="M3.2 1.5l2.3 2.6-1.2 1.8c.8 2 2.5 3.7 4.6 4.6l1.8-1.2 2.6 2.3-1.4 2.3C6.4 13.6 2.4 9.6 1 4.1z"/></svg>
        020 5194 6281
      </li>
      <li>
        <svg viewBox="0 0 16 16" aria-hidden="true"><rect x="4" y="1" width="8" height="14" rx="1.5" fill="none" stroke="var(--brand-green)" stroke-width="1.6"/><circle cx="8" cy="12.5" r="0.9" fill="var(--brand-green)"/></svg>
        07845139072
      </li>
      <li>
        <svg viewBox="0 0 16 16" aria-hidden="true"><rect x="1.5" y="3.5" width="13" height="9" fill="var(--brand-green)"/><path d="M1.5 3.5L8 9l6.5-5.5" fill="none" stroke="var(--panel-green)" stroke-width="1.3"/></svg>
        tomasz@varkelt.co.uk
      </li>
      <li>
        <svg viewBox="0 0 16 16" aria-hidden="true"><circle cx="8" cy="8" r="6.5" fill="var(--brand-green)"/><path d="M1.5 8h13M8 1.5c-2.5 3-2.5 10 0 13M8 1.5c2.5 3 2.5 10 0 13" fill="none" stroke="var(--panel-green)" stroke-width="1"/></svg>
        www.varkelt.co.uk
      </li>
    </ul>
  </div>

  <p class="brand-name"><span class="brand-word">Varkelt</span><span class="brand-suffix">Construction Ltd</span></p>
</section>

<section class="card card--back" aria-label="Business card back">
  <p class="brand-name"><span class="brand-word">Varkelt</span><span class="brand-suffix">Construction Ltd</span></p>

  <svg width="0" height="0" style="position:absolute" aria-hidden="true">
    <symbol id="tick-mark" viewBox="0 0 15 13"><path d="M1.5 7l4 4 8-9.5" fill="none" stroke="var(--brand-green)" stroke-width="2.2"/></symbol>
  </svg>

  <div class="service-list">
    <p>Kitchen Renovations <svg class="tick"><use href="#tick-mark"/></svg> Bathroom Renovations <svg class="tick"><use href="#tick-mark"/></svg> House Renovations</p>
    <p>Garage Conversions <svg class="tick"><use href="#tick-mark"/></svg> Extensions <svg class="tick"><use href="#tick-mark"/></svg> Loft Conversions <svg class="tick"><use href="#tick-mark"/></svg> Conservatories</p>
    <p>Carpentry <svg class="tick"><use href="#tick-mark"/></svg> Tiling <svg class="tick"><use href="#tick-mark"/></svg> Electrical <svg class="tick"><use href="#tick-mark"/></svg> Plumbing &amp; Heating <svg class="tick"><use href="#tick-mark"/></svg> Bricklaying</p>
    <p>Landscaping <svg class="tick"><use href="#tick-mark"/></svg> Decorating <svg class="tick"><use href="#tick-mark"/></svg> Plastering</p>
  </div>
</section>

</body>
</html>
```